Detail Shop Business card design

i need a business card design for my new detailing company called 'Brisk's Polish Works'. i want an all black and white design . simple, direct and to the point. i want the designer to choose a fitting font to match the logothe front should have logo, address, phone and email and the back side should have a slogan and text indicating that we offer services on anything including cars, trucks, motorcycles and RVs. slogan will read "we take pride in your ride"
maybe also very small on the back side the IG icon with Brisks_Polish_Works

phone 208.417.6352
address 3847 E Larkin Ave
Spokane WA 99214
email: BrisksPolish@mailvexo.com

Target Market(s)

all ages , auto enthusiasts

Industry/Entity Type

Automotive

Contact Information for Business Card

the front should have logo, address, phone and email and the back side should have a slogan and text indicating that we offer services on anything including cars, trucks, motorcycles and RVs. slogan will read "we take pride in your ride"

phone 208.417.6352
address 3847 E Larkin Ave
Spokane WA 99214

Colors
000000
ffffff

Requirements
Must have
• bold font and very simple design with good spacing
Nice to have
• anything creative from the designer indicating we service any types of vehicles
Should not have
• any colors ,

```html
<!DOCTYPE html>
<html lang="en">
<head>
<meta charset="utf-8">
<title>Brisk's Polish Works – Business Card</title>
<link href="https://fonts.googleapis.com/css2?family=Roboto:wght@400;700&family=Roboto+Condensed:wght@400;700&display=swap" rel="stylesheet">
<style>
  :root {
    --ink: #000000;
    --paper: #ffffff;
    --muted: #3a3a3a;
    --stage: #e6e6e6;
    --art-dark: #1a1a1a;
    --art-light: #9a9a9a;
  }
  * { box-sizing: border-box; margin: 0; padding: 0; }
  html, body {
    width: 1200px; height: 886px; overflow: hidden;
    background: var(--stage);
  }
  .stage {
    position: relative; width: 1200px; height: 886px;
    display: flex; justify-content: center; align-items: center; gap: 80px;
  }
  .card {
    width: 340px; height: 595px;
    background: var(--paper);
    box-shadow: 0 6px 22px rgba(0,0,0,.18);
    position: relative;
    color: var(--ink);
  }

  /* Front */
  .front-art {
    position: absolute; left: 40px; top: 200px;
    width: 260px; height: 110px;
    background: linear-gradient(180deg, var(--art-dark) 0%, var(--art-dark) 70%, var(--art-light) 100%);
    border-radius: 40px 40px 10px 10px;
  }
  .front-rule {
    position: absolute; left: 70px; top: 336px;
    width: 200px; height: 3px; background: var(--ink);
  }
  .front-rule.lower { top: 410px; }
  .person {
    position: absolute; left: 0; top: 352px; width: 100%;
    text-align: center;
    font-family: "Roboto", Arial, sans-serif;
  }
  .person-name { font-weight: 700; font-size: 19px; letter-spacing: .5px; }
  .person-role { font-size: 13px; color: var(--muted); letter-spacing: 1px; margin-top: 3px; }
  .contact {
    position: absolute; left: 34px; top: 428px; right: 20px;
    font-family: "Roboto", Arial, sans-serif;
    font-size: 12.5px; line-height: 20px; color: var(--muted);
  }
  .contact b { color: var(--ink); }

  /* Back */
  .brand-name {
    position: absolute; left: 0; top: 250px; width: 100%;
    text-align: center;
    font-family: "Roboto Condensed", Arial, sans-serif;
    font-weight: 700; font-size: 28px; color: var(--ink);
    text-transform: uppercase; letter-spacing: 1px;
  }
  .back-rule {
    position: absolute; left: 40px; width: 260px; height: 1px; background: var(--ink);
  }
  .back-rule.top { top: 390px; }
  .back-rule.bottom { top: 470px; }
  .tagline {
    position: absolute; left: 0; top: 400px; width: 100%; text-align: center;
    font-family: "Roboto Condensed", Arial, sans-serif;
  }
  .slogan { font-weight: 700; font-size: 18px; letter-spacing: .6px; text-transform: uppercase; }
  .services { font-size: 13px; line-height: 16px; margin-top: 4px; }
</style>
</head>
<body>
<main class="stage">
  <section class="card card-front">
    <div class="front-art" role="img" aria-label="Black and white illustration of a classic hot rod car in side view"></div>
    <div class="front-rule"></div>
    <div class="person">
      <div class="person-name">DALE WARNER</div>
      <div class="person-role">CEO/FOUNDER</div>
    </div>
    <div class="front-rule lower"></div>
    <div class="contact">
      <div>3847 E Larkin Ave Spokane WA 99214</div>
      <div><b>P:</b> 208.417.6352 <b>M:</b> 208 553 7140</div>
      <div><b>E:</b> BrisksPolish@mailvexo.com</div>
      <div><b>W:</b> www.briskspolishworks.com</div>
    </div>
  </section>

  <section class="card card-back">
    <div class="brand-name">Brisk's Polish Works</div>
    <div class="back-rule top"></div>
    <div class="tagline">
      <div class="slogan">We take pride in your ride</div>
      <div class="services">we offer services on anything including cars,<br>trucks, motorcycles &amp; RVs</div>
    </div>
    <div class="back-rule bottom"></div>
  </section>
</main>
</body>
</html>
```